Professional Services - letterhead / business cards

The company (velmora partners) will provide services to Investment Funds and large investors in Spain. I have recently chosen a logo that I am attaching.

I would like a simple stationary design that i could use as letter head, business cards and "with compliments" cards.

I am not quite sure which color I will mostly use for the logo, in the email signature I will probably lean towards the white background and grey letters. I am attaching my favourite options.

Target Market(s)

Large Multinationals, Investment funds and Law firms

Industry/Entity Type

Business

Requirements
Must have
• my details are:
Luis R. Abadal
Velmora Partners S.L.
Casa de Torrelumbre
Calle de Vientoalto 27
28014 Madrid
T: +34 (91) 387-2265
M: +34 (646) 819-054
e-mail: labadal@velmorapartners.com

```html
<!DOCTYPE html>
<html lang="en">
<head>
<meta charset="utf-8">
<title>Velmora Partners – Stationery</title>
<link href="https://fonts.googleapis.com/css2?family=Questrial&family=PT+Sans:wght@400;700&family=Lobster&display=swap" rel="stylesheet">
<style>
  :root {
    --navy: #232a6e;
    --grey: #a9abad;
    --grey-dark: #6d6e70;
    --paper: #ffffff;
    --paper-shade: #ececec;
    --backdrop: #e9e7e3;
    --line: #b9babc;
  }
  * { box-sizing: border-box; margin: 0; padding: 0; }
  html, body { width: 1200px; height: 452px; overflow: hidden; }
  body { background: var(--backdrop); font-family: "PT Sans", sans-serif; color: var(--grey-dark); }
  .canvas { position: relative; width: 1200px; height: 452px; }

  .sheet {
    position: absolute;
    background: linear-gradient(150deg, var(--paper) 55%, var(--paper-shade));
    box-shadow: 0 1px 3px rgba(0,0,0,.18);
  }
  .brand-band {
    position: absolute; left: 0; right: 0; bottom: 0;
    background: linear-gradient(100deg, var(--grey) 40%, var(--paper) 40% 41.2%, var(--navy) 41.2%);
  }
  .wordmark {
    position: absolute;
    font-family: "Questrial", sans-serif;
    color: var(--navy);
    white-space: nowrap;
    line-height: 1;
  }
  .details { position: absolute; font-size: 6px; line-height: 1.45; white-space: nowrap; }
  .details--right { text-align: right; }
  .divider { position: absolute; width: 1px; background: var(--line); }
  .icon { display: inline-block; width: 6px; height: 6px; vertical-align: -1px; margin-right: 3px; }

  /* Letterhead */
  .letterhead { left: 4px; top: 8px; width: 337px; height: 437px; }
  .letterhead .wordmark { left: 14px; top: 20px; font-size: 19px; }
  .letterhead .divider { left: 248px; top: 8px; height: 42px; }
  .letterhead .details { left: 253px; top: 10px; }
  .letterhead .brand-band { height: 6px; }

  /* Envelopes */
  .envelope-back { left: 456px; top: 10px; width: 376px; height: 169px; background: var(--paper); }
  .envelope-back svg, .envelope-open svg { position: absolute; left: 0; top: 0; }
  .envelope-back .wordmark { left: 0; right: 0; top: 28px; text-align: center; font-size: 20px; color: var(--paper); }
  .envelope-open { left: 373px; top: 83px; width: 377px; height: 168px; background: var(--paper); }
  .envelope-open .wordmark { left: 0; right: 0; top: 22px; text-align: center; font-size: 22px; }
  .envelope-front { left: 413px; top: 158px; width: 377px; height: 168px; }
  .envelope-front .wordmark { left: 10px; top: 14px; font-size: 18px; }
  .envelope-front .details { left: 10px; top: 40px; }
  .envelope-front .brand-band { height: 5px; }

  /* Compliments card */
  .compliments { left: 865px; top: 159px; width: 304px; height: 155px; }
  .compliments .wordmark { left: 0; right: 0; top: 30px; text-align: center; font-size: 24px; }
  .compliments .greeting {
    position: absolute; left: 0; right: 0; top: 82px; text-align: center;
    font-family: "Lobster", cursive; font-size: 16px; color: var(--navy);
  }
  .compliments .details--right { right: 162px; top: 111px; }
  .compliments .divider { left: 156px; top: 109px; height: 34px; }
  .compliments .details--contact { left: 162px; top: 111px; }
  .compliments .brand-band { height: 5px; }
  .caption {
    position: absolute; left: 865px; top: 322px; width: 304px; text-align: center;
    font-family: "PT Sans", sans-serif; font-size: 18px; color: var(--grey-dark);
  }

  /* Business cards */
  .card { top: 353px; width: 170px; height: 96px; }
  .card--front { left: 379px; }
  .card--back { left: 556px; }
  .card--grey { left: 733px; background: var(--grey); }
  .card .wordmark { font-size: 14px; }
  .card--front .wordmark { left: 18px; top: 16px; }
  .card--back .wordmark, .card--grey .wordmark { left: 0; right: 0; top: 41px; text-align: center; }
  .card--grey .wordmark { color: var(--paper); }
  .card .holder { position: absolute; right: 90px; top: 45px; text-align: right; font-size: 5px; line-height: 1.4; white-space: nowrap; }
  .card .holder-name { font-size: 7px; font-weight: 700; color: var(--navy); }
  .card .divider { left: 84px; top: 46px; height: 28px; }
  .card .details--contact { left: 87px; top: 48px; font-size: 4.6px; }
  .card .brand-band { height: 4px; }
</style>
</head>
<body>
<main class="canvas">

  <section class="sheet letterhead" aria-label="Letterhead">
    <div class="wordmark">velmora partners</div>
    <div class="divider"></div>
    <div class="details">
      <div><svg class="icon" viewBox="0 0 10 10"><path d="M2 1l2 2-1 1.5q1 2 2.5 2.5L7 6l2 2-1.5 1.5Q3 9 .5 2.5z" fill="currentColor"/></svg>+34 (91) 387-2265</div>
      <div>Casa de Torrelumbre</div>
      <div>Calle de Vientoalto 27</div>
      <div>28014 Madrid</div>
    </div>
    <div class="brand-band"></div>
  </section>

  <section class="sheet envelope-back" aria-label="Envelope, back with flap">
    <svg width="376" height="80" viewBox="0 0 376 80" aria-hidden="true">
      <path d="M0 0H376V6Q368 34 330 44L200 76Q186 80 172 76L46 44Q8 34 0 6Z" fill="var(--grey)"/>
    </svg>
    <div class="wordmark">velmora</div>
  </section>

  <section class="sheet envelope-open" aria-label="Envelope, open flap">
    <svg width="377" height="70" viewBox="0 0 377 70" aria-hidden="true">
      <path d="M0.5 0.5H376.5V4Q370 28 332 36L205 64Q189 68 173 64L46 36Q8 28 0.5 4Z" fill="none" stroke="#333" stroke-width="1"/>
    </svg>
    <div class="wordmark">velmora</div>
  </section>

  <section class="sheet envelope-front" aria-label="Envelope, front">
    <div class="wordmark">velmora partners</div>
    <div class="details">Casa de Torrelumbre, Calle de Vientoalto 27, 28014 Madrid</div>
    <div class="brand-band"></div>
  </section>

  <section class="sheet compliments" aria-label="With compliments card">
    <div class="wordmark">velmora partners</div>
    <div class="greeting">With Compliments</div>
    <div class="details details--right">
      <div>Casa de Torrelumbre</div>
      <div>Calle de Vientoalto 27</div>
      <div>28014 Madrid</div>
    </div>
    <div class="divider"></div>
    <div class="details details--contact">
      <div>T +34 (91) 387-2265</div>
      <div>M +34 (646) 819-054</div>
      <div>E labadal@velmorapartners.com</div>
    </div>
    <div class="brand-band"></div>
  </section>
  <p class="caption">Compliments</p>

  <section class="sheet card card--front" aria-label="Business card, front">
    <div class="wordmark">velmora partners</div>
    <div class="holder">
      <div class="holder-name">Luis R. Abadal</div>
      <div>Velmora Partners S.L.</div>
      <div>Casa de Torrelumbre</div>
      <div>Calle de Vientoalto 27</div>
      <div>28014 Madrid</div>
    </div>
    <div class="divider"></div>
    <div class="details details--contact">
      <div>T +34 (91) 387-2265</div>
      <div>M +34 (646) 819-054</div>
      <div>E labadal@velmorapartners.com</div>
    </div>
    <div class="brand-band"></div>
  </section>

  <section class="sheet card card--back" aria-label="Business card, white back">
    <div class="wordmark">velmora partners</div>
  </section>

  <section class="sheet card card--grey" aria-label="Business card, grey back">
    <div class="wordmark">velmora partners</div>
  </section>

</main>
</body>
</html>
```